Brisk Coatings business card for residential and commercial painting

A clean, professional design. Easy to read
Eye catching and elegant
Front could have some color variations
On the back of card I would like all black with signature logo

*Attached is my current business card and the items I want displayed

Contact Information for Business Card

Email, phone number, website, and owner name

Font styles to use
Serif

Requirements
Must have
• My logo with cool design and perhaps some paint splatter

```html
<!DOCTYPE html>
<html lang="en">
<head>
<meta charset="utf-8">
<title>Brisk Coatings – Business Card</title>
<link rel="stylesheet" href="https://fonts.googleapis.com/css2?family=Roboto:wght@400;500&family=Roboto+Condensed:wght@700&display=swap">
<style>
  :root {
    --backdrop: #3a3a3a;
    --card: #1e1e1f;
    --ink-grey: #9a9a9a;
    --ink-white: #f2f2f2;
    --accent-blue: #1b86d8;
  }
  * { box-sizing: border-box; margin: 0; padding: 0; }
  html, body {
    width: 799px; height: 1200px; overflow: hidden;
    background: var(--backdrop);
    font-family: "Roboto", Arial, sans-serif;
  }
  .canvas {
    position: relative; width: 799px; height: 1200px;
  }
  .card {
    position: absolute; left: 80px;
    width: 640px; height: 366px;
    background: var(--card);
    border-radius: 4px;
    box-shadow: 0 12px 28px rgba(0,0,0,.45);
  }
  .card-front { top: 124px; }
  .card-back { top: 710px; }

  .wordmark {
    font-family: "Roboto Condensed", Arial, sans-serif;
    font-weight: 700;
    letter-spacing: 1px;
    text-transform: uppercase;
    white-space: nowrap;
  }
  .card-front .wordmark {
    position: absolute; left: 0; right: 0; top: 128px;
    text-align: center; font-size: 58px; color: var(--ink-grey);
  }
  .front-url {
    position: absolute; left: 0; right: 0; top: 206px;
    text-align: center; font-size: 19px; color: var(--ink-white);
    letter-spacing: .5px;
  }
  .front-url .url-name { color: var(--accent-blue); }

  .card-back .wordmark {
    position: absolute; left: 48px; top: 42px;
    font-size: 46px; color: var(--accent-blue);
  }
  .owner {
    position: absolute; left: 48px; top: 196px;
  }
  .owner-name {
    font-size: 22px; font-weight: 500; color: var(--accent-blue);
  }
  .owner-title {
    font-size: 16px; color: var(--ink-white); margin-top: 4px;
  }
  .contact-row {
    position: absolute; left: 48px; right: 40px; top: 290px;
    display: flex; gap: 26px; align-items: center;
    font-size: 15px; color: var(--ink-white);
  }
  .contact-item { display: flex; align-items: center; gap: 8px; white-space: nowrap; }
  .contact-icon { width: 15px; height: 15px; fill: var(--accent-blue); flex: none; }
</style>
</head>
<body>
<main class="canvas">
  <section class="card card-front" aria-label="Card front">
    <div class="wordmark">Brisk Coatings</div>
    <div class="front-url">www.<span class="url-name">briskcoatingstn</span>.com</div>
  </section>

  <section class="card card-back" aria-label="Card back">
    <div class="wordmark">Brisk Coatings</div>
    <div class="owner">
      <div class="owner-name">Marco "MJ"</div>
      <div class="owner-title">Owner - Licensed &amp; Insured</div>
    </div>
    <div class="contact-row">
      <span class="contact-item">
        <svg class="contact-icon" viewBox="0 0 24 24" aria-hidden="true"><path d="M6.6 10.8a15.1 15.1 0 0 0 6.6 6.6l2.2-2.2a1 1 0 0 1 1-.25 11.4 11.4 0 0 0 3.6.57 1 1 0 0 1 1 1V20a1 1 0 0 1-1 1A17 17 0 0 1 3 4a1 1 0 0 1 1-1h3.5a1 1 0 0 1 1 1c0 1.25.2 2.45.57 3.57a1 1 0 0 1-.25 1z"/></svg>
        931-555-0147
      </span>
      <span class="contact-item">
        <svg class="contact-icon" viewBox="0 0 24 24" aria-hidden="true"><path d="M2 5h20v14H2z M3.5 6.5 12 13l8.5-6.5" fill="none" stroke="var(--accent-blue)" stroke-width="2"/></svg>
        office@briskcoatingstn.com
      </span>
      <span class="contact-item">
        <svg class="contact-icon" viewBox="0 0 24 24" aria-hidden="true"><circle cx="12" cy="12" r="9" fill="none" stroke="var(--accent-blue)" stroke-width="2"/><path d="M3 12h18M12 3c3 3 3 15 0 18M12 3c-3 3-3 15 0 18" fill="none" stroke="var(--accent-blue)" stroke-width="1.6"/></svg>
        briskcoatingstn.com
      </span>
    </div>
  </section>
</main>
</body>
</html>
```